Business card design for a dynamic IT consulting company

We need a business card design for a young firm, specialized in the Telecommunications/Consulting industry. The name of the company is Quindor and Partners Business Consulting Ltd. (Short name: Quindor and Partnes)
Quindor = solve read reverse, so we aim to be uncomplicated and solution-oriented. The small pipe in our logo is also related to the word solve. So we need a new business card design, which is simple, eye catching and something non traditional (I would probably prefer a square shaped design rather than a rectangle, but open for suggestions). Attached our logo.

Target Market(s)

Usually our customers are Tier1 Telecoms providers (Q-Netra, Palorix, etc) and their executives.

Industry/Entity Type

Business

Contact Information for Business Card

Name: Bence Tolnavari
Email: b.tolnavari@quindor.hu
Web: www.quindor.hu
Mobile: +36 30 518 2769
Title: Managing Director

Optional:
Company name: Quindor and Partners Ltd.
Address: 1087 Budapest, Tolvenka str. 28/C, Hungary

Font styles to use
Other font styles liked:
• helveticaneue_medium, Prime Regular are used now.

Colors

Designer to choose colors to be used in the design.

Requirements
Must have
• I would like to have a 2 sided design.
Nice to have
• I thought if we make the logo a bit bigger (without the company name), that could go to the back with the company name below. I though, if the pipe in the logo is somehow touchable on the business card, would be nice and unique.

```html
<!DOCTYPE html>
<html lang="en">
<head>
<meta charset="utf-8">
<title>Quindor and Partners – Business Card</title>
<link href="https://fonts.googleapis.com/css2?family=Arimo:wght@400;700&display=swap" rel="stylesheet">
<style>
  :root {
    --backdrop: #5a4738;
    --card-dark: #5c5d60;
    --card-light: #f3f3f3;
    --accent-blue: #0b95d5;
    --accent-magenta: #b3278e;
    --ink-white: #ffffff;
    --ink-grey: #5d5e60;
    --rule: #ffffff;
  }
  * { margin: 0; padding: 0; box-sizing: border-box; }
  html, body {
    width: 1200px;
    height: 960px;
    overflow: hidden;
  }
  body {
    background: var(--backdrop);
    font-family: "Arimo", Helvetica, Arial, sans-serif;
    position: relative;
  }
  .card {
    position: absolute;
    top: 309px;
    width: 343px;
    height: 343px;
    text-align: center;
  }
  .card--front {
    left: 235px;
    background: var(--card-dark);
    color: var(--ink-white);
  }
  .card--back {
    left: 623px;
    background: var(--card-light);
    color: var(--ink-grey);
  }

  /* front */
  .front-mark {
    position: absolute;
    top: 52px;
    left: 0;
    right: 0;
    display: flex;
    justify-content: center;
    align-items: center;
    gap: 7px;
    font-size: 20px;
    font-weight: 700;
    color: var(--ink-white);
  }
  .mark-square {
    width: 9px;
    height: 9px;
    background: var(--accent-magenta);
  }
  .holder-name {
    position: absolute;
    top: 133px;
    left: 0; right: 0;
    font-size: 20px;
    font-weight: 700;
    color: var(--accent-blue);
    letter-spacing: 0.6px;
    line-height: 22px;
  }
  .holder-title {
    position: absolute;
    top: 155px;
    left: 0; right: 0;
    font-size: 16px;
    line-height: 18px;
    letter-spacing: 0.2px;
  }
  .divider {
    position: absolute;
    left: 160px;
    width: 24px;
    height: 1px;
    background: var(--rule);
  }
  .divider--one { top: 186px; }
  .divider--two { top: 247px; }
  .contact {
    position: absolute;
    left: 0; right: 0;
    font-size: 14.5px;
    line-height: 19px;
  }
  .contact--direct { top: 200px; }
  .contact--address { top: 259px; font-size: 14px; }

  /* back */
  .back-lockup {
    position: absolute;
    top: 190px;
    left: 0; right: 0;
  }
  .company-name {
    display: flex;
    justify-content: center;
    align-items: center;
    gap: 7px;
    font-size: 26px;
    font-weight: 400;
    color: var(--ink-grey);
    line-height: 30px;
  }
  .company-name .mark-square { width: 9px; height: 9px; }
  .tagline {
    margin-top: 1px;
    font-size: 8.5px;
    line-height: 10px;
    font-weight: 700;
    letter-spacing: 3.4px;
    color: var(--ink-grey);
  }
  .tagline .sep { color: var(--accent-blue); }
</style>
</head>
<body>
  <section class="card card--front" aria-label="Business card front">
    <div class="front-mark"><span class="mark-square"></span>Quindor</div>
    <h1 class="holder-name">BENCE TOLNAVARI</h1>
    <p class="holder-title">MANAGING DIRECTOR</p>
    <span class="divider divider--one"></span>
    <p class="contact contact--direct">+36 30 518 2769<br>b.tolnavari@quindor.hu</p>
    <span class="divider divider--two"></span>
    <p class="contact contact--address">Quindor and Partners Ltd.,1087 Budapest<br>Tolvenka str. 28/C, Hungary</p>
  </section>

  <section class="card card--back" aria-label="Business card back">
    <div class="back-lockup">
      <div class="company-name"><span class="mark-square"></span>Quindor &amp; Partners</div>
      <p class="tagline">CLARITY <span class="sep">·</span> FOCUS <span class="sep">·</span> RESULT</p>
    </div>
  </section>
</body>
</html>
```